App Design - Career Prep Pal

We require an App Design for our new App called 'Hiring Helper'. This app is essentially an assistant to help Users prepare for job interviews, to help them get hired. <br/><br/>Users who download the App can view common Questions and Answers, save their favourite responses and also view common Interview Tips. <br/><br/>The vision for our App is for Users who are preparing for an interview (1 week before, 1 day before, even 1 hour before), are able to download, view and educate themselves on common questions and responses, and then be confident to land the job. <br/><br/>Our team has developed wireframes to help highlight what each screen should do and include. Please see attached document, which also highlights key requirements for the experience. Feel free to add/remove/edit what you see on these wireframes. Our preference is that you use Adobe XD please.<br/><br/>In terms of design guidelines, we want the experience to be simple, intuitive and 'memorable' to help Users to remember the questions/responses when they are in the interview. <br/><br/>The final design should communicate 'neat and clean professionalism'; we like the design of: jobvista net au<br/><br/>Thank you for reading! Good luck !

Target Market(s)

Professional job seekers

Font styles to use
Sans Serif

Colors

Designer to choose colors to be used in the design.

Requirements
Must have
• Please see my PixelGuild_UX file that I have uploaded
Nice to have
• Could you also please include some ideas on how we can incorporate Advertising into the app screens

```html
<!DOCTYPE html>
<html lang="en">
<head>
<meta charset="utf-8">
<title>Career Prep Pal – Hiring Helper App Screens</title>
<link href="https://fonts.googleapis.com/css2?family=Montserrat:wght@400;500;600;700&display=swap" rel="stylesheet">
<style>
  :root {
    --page: #ffffff;
    --band: #313031;
    --teal: #15a3c2;
    --teal-deep: #0f7f99;
    --teal-photo: #2a8ea6;
    --navy-photo: #123642;
    --shade: rgba(14, 42, 52, 0.82);
    --button: rgba(21, 158, 190, 0.92);
    --button-dark: #202224;
    --white: #ffffff;
    --nav-ink: #6c6f73;
    --status: #1b1b1b;
  }
  * { box-sizing: border-box; margin: 0; padding: 0; }
  html, body { width: 867px; height: 1200px; overflow: hidden; background: var(--page); }
  body { position: relative; font-family: "Montserrat", sans-serif; }

  .band {
    position: absolute; left: 0; top: 0; width: 867px; height: 1200px;
  }

  .screen {
    position: absolute; width: 196px; height: 425px; overflow: hidden;
    background: var(--white);
    box-shadow: 0 10px 24px rgba(0,0,0,0.18);
  }
  .screen--hero { left: 339px; top: 79px; }
  .screen--splash { left: 91px; top: 676px; }
  .screen--menu { left: 347px; top: 676px; }
  .screen--category { left: 602px; top: 676px; }

  .status-bar {
    position: absolute; left: 0; top: 0; width: 100%; height: 13px;
    background: var(--status); color: var(--white);
    font-size: 6px; display: flex; align-items: center; padding: 0 7px;
  }
  .status-bar .dots { letter-spacing: 0.5px; font-weight: 700; margin-right: 5px; }
  .status-bar .app { margin-right: 15px; }
  .status-bar .icons { margin-left: auto; display: flex; gap: 6px; align-items: center; }

  .photo {
    position: absolute; left: 0; top: 13px; width: 100%; height: 368px;
    background: linear-gradient(160deg, #2f7f93 0%, #1d5869 45%, #16414e 100%);
  }
  .photo--bright {
    background: linear-gradient(170deg, #2ba0bb 0%, #2489a3 50%, #1f7d96 100%);
  }

  .header-wave {
    position: absolute; left: 0; top: 13px; width: 100%; height: 40px;
    background: linear-gradient(180deg, #1cb0cd 0%, var(--teal) 100%);
  }
  .title-tab {
    position: absolute; left: 22px; top: 35px; width: 152px; height: 32px;
    background: var(--teal); border-radius: 0 0 16px 16px;
    color: var(--white); font-weight: 700; font-size: 13.5px;
    display: flex; align-items: center; justify-content: center;
  }

  .back {
    position: absolute; left: 6px; top: 28px; width: 12px; height: 8px;
  }

  .shade-circle {
    position: absolute; left: 31px; top: 171px; width: 264px; height: 264px;
    border-radius: 50%; background: var(--shade);
  }
  .tagline {
    position: absolute; left: 74px; top: 246px; width: 122px;
    color: var(--white); font-weight: 700; font-size: 9.4px; line-height: 16.2px;
  }
  .next-arrow { position: absolute; left: 74px; top: 344px; width: 16px; height: 6px; }

  .menu {
    position: absolute; left: 12px; width: 172px;
    display: flex; flex-direction: column;
  }
  .menu--main { top: 103px; gap: 12px; }
  .menu--category { top: 141px; gap: 13px; left: 12px; }
  .menu-button {
    height: 26px; border-radius: 3px; background: var(--button);
    color: var(--white); font-size: 9.6px; font-weight: 500;
    display: flex; align-items: center; justify-content: center;
  }
  .menu-button--active { background: var(--button-dark); box-shadow: 0 3px 6px rgba(0,0,0,0.35); }

  .section-title {
    position: absolute; left: 0; top: 93px; width: 100%; text-align: center;
    color: var(--white); font-size: 9.6px; font-weight: 700;
  }
  .section-hint {
    position: absolute; left: 0; top: 124px; width: 100%; text-align: center;
    color: var(--white); font-size: 8px; font-weight: 400;
  }

  .tab-bar {
    position: absolute; left: 0; bottom: 0; width: 100%; height: 44px;
    background: var(--white); display: flex; justify-content: space-around;
    align-items: center; padding: 0 2px;
  }
  .tab { display: flex; flex-direction: column; align-items: center; gap: 3px;
    color: var(--nav-ink); font-size: 7.6px; width: 48px; }
  .tab svg { width: 13px; height: 13px; }
</style>
</head>
<body>
  <svg class="band" viewBox="0 0 867 1200" aria-hidden="true">
    <polygon points="0,585 867,580 867,887 0,892" fill="var(--band)"/>
  </svg>

  <!-- Hero screen -->
  <section class="screen screen--hero">
    <div class="photo" role="img" aria-label="Photo of a smiling young woman in a checked shirt at a job interview, shaking hands"></div>
    <div class="header-wave"></div>
    <div class="title-tab">Hiring Helper</div>
    <div class="shade-circle"></div>
    <p class="tagline">Your guide to the most common interview questions,and the best responses to help you get hired</p>
    <svg class="next-arrow" viewBox="0 0 16 6"><path d="M0 3h15M12 0.5l3 2.5-3 2.5" stroke="#fff" stroke-width="0.8" fill="none"/></svg>
    <div class="status-bar"><span class="dots">•••</span><span class="app">Hiring Helper</span><span>19:33</span>
      <span class="icons"><svg width="7" height="5" viewBox="0 0 7 5"><path d="M0.5 1.8a4 4 0 0 1 6 0M1.7 3a2.3 2.3 0 0 1 3.6 0" stroke="#fff" stroke-width="0.7" fill="none"/><circle cx="3.5" cy="4.3" r="0.6" fill="#fff"/></svg><svg width="13" height="6" viewBox="0 0 13 6"><rect x="0.4" y="0.4" width="11" height="5.2" rx="1" stroke="#fff" stroke-width="0.7" fill="none"/><rect x="1.5" y="1.5" width="4" height="3" fill="#fff"/><rect x="11.6" y="2" width="1" height="2" fill="#fff"/></svg></span></div>
    <nav class="tab-bar">
      <div class="tab"><svg viewBox="0 0 14 14"><path d="M7 13s-4.5-4.5-4.5-7.5a4.5 4.5 0 0 1 9 0C11.5 8.5 7 13 7 13z" stroke="currentColor" fill="none" stroke-width="0.9"/><circle cx="7" cy="5.5" r="1.6" stroke="currentColor" fill="none" stroke-width="0.9"/></svg>Location</div>
      <div class="tab"><svg viewBox="0 0 14 14"><circle cx="7" cy="7" r="5.8" stroke="currentColor" fill="none" stroke-width="0.9"/><ellipse cx="7" cy="7" rx="2.6" ry="5.8" stroke="currentColor" fill="none" stroke-width="0.9"/><path d="M1.2 7h11.6M2 4h10M2 10h10" stroke="currentColor" stroke-width="0.9"/></svg>Browse</div>
      <div class="tab"><svg viewBox="0 0 14 14"><path d="M7 12.2 1.9 7.1a3 3 0 0 1 5.1-3.7 3 3 0 0 1 5.1 3.7z" stroke="currentColor" fill="none" stroke-width="0.9"/></svg>Favorites</div>
      <div class="tab"><svg viewBox="0 0 14 14"><circle cx="7" cy="4.5" r="3" stroke="currentColor" fill="none" stroke-width="0.9"/><path d="M1.5 13v-1.5a4 4 0 0 1 4-4h3a4 4 0 0 1 4 4V13z" stroke="currentColor" fill="none" stroke-width="0.9"/></svg>Profile</div>
    </nav>
  </section>

  <!-- Splash screen -->
  <section class="screen screen--splash">
    <div class="photo" role="img" aria-label="Photo of a smiling young woman in a checked shirt at a job interview, shaking hands"></div>
    <div class="header-wave"></div>
    <div class="title-tab">Hiring Helper</div>
    <div class="shade-circle"></div>
    <p class="tagline">Your guide to the most common interview questions,and the best responses to help you get hired</p>
    <svg class="next-arrow" viewBox="0 0 16 6"><path d="M0 3h15M12 0.5l3 2.5-3 2.5" stroke="#fff" stroke-width="0.8" fill="none"/></svg>
    <div class="status-bar"><span class="dots">•••</span><span class="app">Hiring Helper</span><span>19:33</span>
      <span class="icons"><svg width="7" height="5" viewBox="0 0 7 5"><path d="M0.5 1.8a4 4 0 0 1 6 0M1.7 3a2.3 2.3 0 0 1 3.6 0" stroke="#fff" stroke-width="0.7" fill="none"/><circle cx="3.5" cy="4.3" r="0.6" fill="#fff"/></svg><svg width="13" height="6" viewBox="0 0 13 6"><rect x="0.4" y="0.4" width="11" height="5.2" rx="1" stroke="#fff" stroke-width="0.7" fill="none"/><rect x="1.5" y="1.5" width="4" height="3" fill="#fff"/><rect x="11.6" y="2" width="1" height="2" fill="#fff"/></svg></span></div>
    <nav class="tab-bar">
      <div class="tab"><svg viewBox="0 0 14 14"><path d="M7 13s-4.5-4.5-4.5-7.5a4.5 4.5 0 0 1 9 0C11.5 8.5 7 13 7 13z" stroke="currentColor" fill="none" stroke-width="0.9"/><circle cx="7" cy="5.5" r="1.6" stroke="currentColor" fill="none" stroke-width="0.9"/></svg>Location</div>
      <div class="tab"><svg viewBox="0 0 14 14"><circle cx="7" cy="7" r="5.8" stroke="currentColor" fill="none" stroke-width="0.9"/><ellipse cx="7" cy="7" rx="2.6" ry="5.8" stroke="currentColor" fill="none" stroke-width="0.9"/><path d="M1.2 7h11.6M2 4h10M2 10h10" stroke="currentColor" stroke-width="0.9"/></svg>Browse</div>
      <div class="tab"><svg viewBox="0 0 14 14"><path d="M7 12.2 1.9 7.1a3 3 0 0 1 5.1-3.7 3 3 0 0 1 5.1 3.7z" stroke="currentColor" fill="none" stroke-width="0.9"/></svg>Favorites</div>
      <div class="tab"><svg viewBox="0 0 14 14"><circle cx="7" cy="4.5" r="3" stroke="currentColor" fill="none" stroke-width="0.9"/><path d="M1.5 13v-1.5a4 4 0 0 1 4-4h3a4 4 0 0 1 4 4V13z" stroke="currentColor" fill="none" stroke-width="0.9"/></svg>Profile</div>
    </nav>
  </section>

  <!-- Main menu screen -->
  <section class="screen screen--menu">
    <div class="photo photo--bright" role="img" aria-label="Teal-tinted photo of a job interview handshake across a desk"></div>
    <div class="header-wave"></div>
    <div class="title-tab">Hiring Helper</div>
    <div class="menu menu--main">
      <div class="menu-button menu-button--active">View Questions &amp; Responses</div>
      <div class="menu-button">My Question Portfolio</div>
      <div class="menu-button">Interview Tips</div>
    </div>
    <div class="status-bar"><span class="dots">•••</span><span class="app">Hiring Helper</span><span>19:33</span>
      <span class="icons"><svg width="7" height="5" viewBox="0 0 7 5"><path d="M0.5 1.8a4 4 0 0 1 6 0M1.7 3a2.3 2.3 0 0 1 3.6 0" stroke="#fff" stroke-width="0.7" fill="none"/><circle cx="3.5" cy="4.3" r="0.6" fill="#fff"/></svg><svg width="13" height="6" viewBox="0 0 13 6"><rect x="0.4" y="0.4" width="11" height="5.2" rx="1" stroke="#fff" stroke-width="0.7" fill="none"/><rect x="1.5" y="1.5" width="4" height="3" fill="#fff"/><rect x="11.6" y="2" width="1" height="2" fill="#fff"/></svg></span></div>
    <nav class="tab-bar">
      <div class="tab"><svg viewBox="0 0 14 14"><path d="M7 13s-4.5-4.5-4.5-7.5a4.5 4.5 0 0 1 9 0C11.5 8.5 7 13 7 13z" stroke="currentColor" fill="none" stroke-width="0.9"/><circle cx="7" cy="5.5" r="1.6" stroke="currentColor" fill="none" stroke-width="0.9"/></svg>Location</div>
      <div class="tab"><svg viewBox="0 0 14 14"><circle cx="7" cy="7" r="5.8" stroke="currentColor" fill="none" stroke-width="0.9"/><ellipse cx="7" cy="7" rx="2.6" ry="5.8" stroke="currentColor" fill="none" stroke-width="0.9"/><path d="M1.2 7h11.6M2 4h10M2 10h10" stroke="currentColor" stroke-width="0.9"/></svg>Browse</div>
      <div class="tab"><svg viewBox="0 0 14 14"><path d="M7 12.2 1.9 7.1a3 3 0 0 1 5.1-3.7 3 3 0 0 1 5.1 3.7z" stroke="currentColor" fill="none" stroke-width="0.9"/></svg>Favorites</div>
      <div class="tab"><svg viewBox="0 0 14 14"><circle cx="7" cy="4.5" r="3" stroke="currentColor" fill="none" stroke-width="0.9"/><path d="M1.5 13v-1.5a4 4 0 0 1 4-4h3a4 4 0 0 1 4 4V13z" stroke="currentColor" fill="none" stroke-width="0.9"/></svg>Profile</div>
    </nav>
  </section>

  <!-- Category screen -->
  <section class="screen screen--category">
    <div class="photo photo--bright" role="img" aria-label="Teal-tinted photo of a job interview handshake across a desk"></div>
    <div class="header-wave"></div>
    <svg class="back" viewBox="0 0 12 8"><path d="M11 4H1.5M4 1 1 4l3 3" stroke="#fff" stroke-width="1.2" fill="none"/></svg>
    <div class="title-tab">Hiring Helper</div>
    <h2 class="section-title">View Questions &amp; Responses</h2>
    <p class="section-hint">Select Your Question Category</p>
    <div class="menu menu--category">
      <div class="menu-button">Behavioural</div>
      <div class="menu-button">Situational</div>
      <div class="menu-button">Motivational</div>
      <div class="menu-button">Technical</div>
      <div class="menu-button menu-button--active">View All</div>
    </div>
    <div class="status-bar"><span class="dots">•••</span><span class="app">Hiring Helper</span><span>19:33</span>
      <span class="icons"><svg width="7" height="5" viewBox="0 0 7 5"><path d="M0.5 1.8a4 4 0 0 1 6 0M1.7 3a2.3 2.3 0 0 1 3.6 0" stroke="#fff" stroke-width="0.7" fill="none"/><circle cx="3.5" cy="4.3" r="0.6" fill="#fff"/></svg><svg width="13" height="6" viewBox="0 0 13 6"><rect x="0.4" y="0.4" width="11" height="5.2" rx="1" stroke="#fff" stroke-width="0.7" fill="none"/><rect x="1.5" y="1.5" width="4" height="3" fill="#fff"/><rect x="11.6" y="2" width="1" height="2" fill="#fff"/></svg></span></div>
    <nav class="tab-bar">
      <div class="tab"><svg viewBox="0 0 14 14"><path d="M7 13s-4.5-4.5-4.5-7.5a4.5 4.5 0 0 1 9 0C11.5 8.5 7 13 7 13z" stroke="currentColor" fill="none" stroke-width="0.9"/><circle cx="7" cy="5.5" r="1.6" stroke="currentColor" fill="none" stroke-width="0.9"/></svg>Location</div>
      <div class="tab"><svg viewBox="0 0 14 14"><circle cx="7" cy="7" r="5.8" stroke="currentColor" fill="none" stroke-width="0.9"/><ellipse cx="7" cy="7" rx="2.6" ry="5.8" stroke="currentColor" fill="none" stroke-width="0.9"/><path d="M1.2 7h11.6M2 4h10M2 10h10" stroke="currentColor" stroke-width="0.9"/></svg>Browse</div>
      <div class="tab"><svg viewBox="0 0 14 14"><path d="M7 12.2 1.9 7.1a3 3 0 0 1 5.1-3.7 3 3 0 0 1 5.1 3.7z" stroke="currentColor" fill="none" stroke-width="0.9"/></svg>Favorites</div>
      <div class="tab"><svg viewBox="0 0 14 14"><circle cx="7" cy="4.5" r="3" stroke="currentColor" fill="none" stroke-width="0.9"/><path d="M1.5 13v-1.5a4 4 0 0 1 4-4h3a4 4 0 0 1 4 4V13z" stroke="currentColor" fill="none" stroke-width="0.9"/></svg>Profile</div>
    </nav>
  </section>
</body>
</html>
```